business card deign

Logo needs the following on it.
1. attached logo
2. Tagline - "If it keeps things chilled or the fun rolling...count us in!"
3. Name- Dalton Pikes, Founder and CPO
4. Address - 412 E. Carver Avenue, Ste 2207, Ridgeport, SC. 33917
5. Phone - 555.318.4726

```html
<!DOCTYPE html>
<html lang="en">
<head>
<meta charset="utf-8">
<title>Marlow Business Card</title>
<link href="https://fonts.googleapis.com/css2?family=Open+Sans:wght@400;600;700;800&display=swap" rel="stylesheet">
<style>
  :root {
    --stage: #222222;
    --card-black: #121212;
    --card-white: #ffffff;
    --ink: #0d0d0d;
    --paper-text: #ffffff;
    --pattern-tone: #2a2a2a;
    --art-tone: #1a1a1a;
  }
  html, body {
    margin: 0;
    padding: 0;
    width: 1200px;
    height: 780px;
    overflow: hidden;
    background: var(--stage);
    font-family: "Open Sans", sans-serif;
  }
  .canvas {
    position: relative;
    width: 1200px;
    height: 780px;
    display: flex;
    align-items: center;
    justify-content: center;
    gap: 40px;
  }
  .card {
    position: relative;
    width: 540px;
    height: 309px;
    border-radius: 22px;
    overflow: hidden;
    box-shadow: 0 14px 30px rgba(0,0,0,0.5);
  }

  /* Front */
  .card-front { background: var(--card-black); }
  .front-pattern {
    position: absolute;
    inset: 0;
    background: linear-gradient(135deg, var(--card-black) 0%, var(--pattern-tone) 55%, #3a3a3a 100%);
    opacity: 0.8;
  }
  .front-brand {
    position: absolute;
    inset: 0;
    display: flex;
    align-items: center;
    justify-content: center;
    gap: 14px;
  }
  .brand-dot {
    width: 14px;
    height: 14px;
    border-radius: 50%;
    background: var(--paper-text);
  }
  .front-wordmark {
    color: var(--paper-text);
    font-weight: 700;
    font-size: 34px;
    letter-spacing: 14px;
  }

  /* Back */
  .card-back { background: var(--card-white); }
  .back-band-column {
    position: absolute;
    left: 300px; right: 0; top: 118px; bottom: 0;
    background: var(--card-black);
  }
  .back-band-base {
    position: absolute;
    left: 200px; right: 0; top: 182px; bottom: 0;
    background: var(--card-black);
  }
  .name-marker {
    position: absolute;
    left: 0; top: 36px;
    width: 9px; height: 46px;
    background: var(--ink);
  }
  .person {
    position: absolute;
    left: 24px; top: 30px;
    color: var(--ink);
  }
  .person-name {
    margin: 0;
    font-weight: 800;
    font-size: 24px;
    line-height: 1.1;
  }
  .person-title {
    margin: 2px 0 0;
    font-weight: 400;
    font-size: 14px;
  }
  .back-wordmark {
    position: absolute;
    right: 28px; top: 50px;
    color: var(--ink);
    font-weight: 700;
    font-size: 22px;
    letter-spacing: 10px;
  }
  .feature-art {
    position: absolute;
    left: 150px; top: 176px;
    width: 150px; height: 133px;
    background: linear-gradient(180deg, #2b2b2b 0%, var(--art-tone) 100%);
    border-radius: 60px 60px 0 0;
  }
  .contact {
    position: absolute;
    right: 22px; top: 130px;
    text-align: right;
    color: var(--paper-text);
    font-size: 12px;
    line-height: 1.35;
  }
  .tagline { margin: 0 0 10px; }
  .contact-line {
    margin: 0 0 8px;
    display: flex;
    justify-content: flex-end;
    align-items: flex-start;
    gap: 6px;
  }
  .contact-line svg { flex: none; margin-top: 2px; }
</style>
</head>
<body>
<main class="canvas">
  <section class="card card-front" aria-label="Card front">
    <div class="front-pattern" role="img" aria-label="Repeated brand mark pattern"></div>
    <div class="front-brand">
      <span class="brand-dot"></span>
      <span class="front-wordmark">MARLOW</span>
    </div>
  </section>

  <section class="card card-back" aria-label="Card back">
    <div class="back-band-column"></div>
    <div class="back-band-base"></div>
    <div class="feature-art" role="img" aria-label="Large kangaroo silhouette illustration"></div>

    <div class="name-marker"></div>
    <div class="person">
      <h1 class="person-name">Dalton Pikes</h1>
      <p class="person-title">Founder and CPO</p>
    </div>

    <div class="back-wordmark">MARLOW</div>

    <div class="contact">
      <p class="tagline">If it keeps things chilled or<br>the fun rolling...count us in!</p>
      <p class="contact-line">555.318.4726
        <svg width="11" height="11" viewBox="0 0 24 24" aria-hidden="true"><path fill="#fff" d="M6.6 10.8a15.1 15.1 0 0 0 6.6 6.6l2.2-2.2c.3-.3.7-.4 1-.2 1.1.4 2.3.6 3.6.6.6 0 1 .4 1 1V20c0 .6-.4 1-1 1A17 17 0 0 1 3 4c0-.6.4-1 1-1h3.5c.6 0 1 .4 1 1 0 1.3.2 2.5.6 3.6.1.3 0 .7-.2 1z"/></svg>
      </p>
      <p class="contact-line">412 E. Carver Avenue,<br>Ste 2207, Ridgeport, SC. 33917
        <svg width="11" height="13" viewBox="0 0 24 28" aria-hidden="true"><path fill="none" stroke="#fff" stroke-width="2.5" d="M12 26s8-8.5 8-15a8 8 0 0 0-16 0c0 6.5 8 15 8 15z"/><circle cx="12" cy="11" r="3" fill="#fff"/></svg>
      </p>
    </div>
  </section>
</main>
</body>
</html>
```